International emerging specialist Research and Development Company focused on plant-based medicine

We need a powerpoint design for a new company based in British Columbia, Canada called Tavrel Phytocor. We are focused on developing plant-based medicines. The company is driven by its experience in research and development work in plant genetics, cultivation techniques, natural medicines, biochemistry, agriculture and technologies. Tavrel will research, develop and produce very unique and specific cultivars from the plant kingdom needed for specific ailments in medical patients. We would like to see designs that use our current logo and its colour scheme. The final design should communicate financial safety, growth, and research and development.

```html
<!DOCTYPE html>
<html lang="en">
<head>
<meta charset="utf-8">
<title>Tavrel Phytocor – Presentation Template</title>
<link rel="stylesheet" href="https://fonts.googleapis.com/css2?family=Roboto+Condensed:wght@400;700&family=Open+Sans:wght@400;600;700&display=swap">
<style>
:root{
  --red:#d7141f;
  --red-dark:#a3111b;
  --red-mid:#c9202a;
  --pink:#f7d9da;
  --row-grey:#e3e3e3;
  --slide-bg:#f1f1f1;
  --band:#cfcfcf;
  --ink:#444;
  --muted:#9a9a9a;
  --slate:#5b5b5b;
  --steel:#8e9ea3;
  --navy:#4c4f63;
  --white:#fff;
  --stage:#000;
}
*{box-sizing:border-box;margin:0;padding:0}
html,body{width:1200px;height:905px;overflow:hidden;background:var(--stage)}
body{position:relative;font-family:"Open Sans",Arial,sans-serif;color:var(--ink)}
.slide{position:absolute;width:380px;height:283px;background:var(--slide-bg);overflow:hidden}
.slide::after{content:"";position:absolute;left:0;right:0;bottom:0;height:10px;background:var(--band)}
.col-1{left:14px}.col-2{left:410px}.col-3{left:806px}
.row-1{top:11px}.row-2{top:305px}.row-3{top:600px}
.header{position:absolute;left:0;top:0;width:100%;height:30px;background:var(--red);display:flex;align-items:center;justify-content:space-between;padding:0 9px 0 10px}
.header-title{font-family:"Roboto Condensed",Arial,sans-serif;color:var(--white);font-size:18px;letter-spacing:.1px;white-space:nowrap}
.brand{display:flex;align-items:center;gap:4px;white-space:nowrap}
.brand-dot{width:9px;height:9px;border-radius:50%;background:var(--white);flex:none}
.brand-name{font-family:"Open Sans",Arial,sans-serif;font-weight:400;color:var(--white);font-size:15px;line-height:1}
.abs{position:absolute}
.lorem{font-size:5.2px;line-height:9.2px;color:var(--muted);overflow:hidden}
.red-head{font-size:7.2px;font-weight:700;color:var(--red);white-space:nowrap}
.bullet-head{font-size:7.4px;font-weight:700;color:var(--red);display:flex;align-items:center;gap:5px;white-space:nowrap}
.bullet-head::before{content:"";width:6px;height:6px;border-radius:50%;border:1.5px solid var(--red);flex:none}
/* cover slides */
.cover-block{position:absolute;left:250px;top:122px;white-space:nowrap}
.cover-title{font-family:"Roboto Condensed",Arial,sans-serif;font-size:17px;line-height:20px;color:#666}
.cover-title .accent{color:var(--red)}
.cover-sub{font-size:5.4px;line-height:9.4px;color:var(--muted);margin-top:3px}
.cover-stripe{position:absolute;left:0;right:0;bottom:0;height:12px;background:var(--red);z-index:1}
.cover-red{position:absolute;left:0;top:0;width:100%;height:181px;background:var(--red)}
.cover-brand{position:absolute;left:258px;top:226px;white-space:nowrap}
.cover-brand .brand-dot{width:15px;height:15px;background:var(--red)}
.cover-brand .brand-name{font-size:26px;color:#555}
.cover-brand .brand-sub{display:block;margin:1px 0 0 21px;font-size:7px;letter-spacing:2.5px;color:#555;line-height:1}
/* table */
.data-table{position:absolute;left:32px;top:104px;width:316px;border-collapse:collapse;font-size:5.6px}
.data-table th{background:var(--red);color:var(--white);font-size:7px;font-weight:700;height:19px;text-align:left;padding-left:8px}
.data-table td{height:20px;padding-left:8px;color:#555;border-bottom:1px solid var(--white)}
.data-table tr:nth-child(even) td{background:var(--row-grey)}
.data-table tr:nth-child(odd) td{background:var(--pink)}
/* paragraphs */
.para-head{font-size:8.5px;color:#555;font-weight:600}
/* timeline */
.year{position:absolute;width:34px;height:34px;border-radius:50%;background:var(--red);border:3px solid #ddd;color:var(--white);font-size:9px;font-weight:700;display:flex;align-items:center;justify-content:center;z-index:2}
.year.grey{background:var(--slate)}
.t-card{position:absolute;top:144px;width:104px;height:125px;background:var(--white);border:1px solid #c9d3dd;border-radius:2px;z-index:1}
.t-card-head{height:18px;background:var(--red);color:var(--white);font-size:6.6px;font-weight:700;text-align:center;line-height:18px}
.t-card.grey .t-card-head{background:var(--slate)}
.t-card p{font-size:5.2px;line-height:9.3px;color:#666;padding:5px 10px}
.t-line{position:absolute;left:60px;top:153px;width:260px;height:1px;background:#bbb}
/* chart */
.axis-label{position:absolute;left:34px;font-size:5.4px;color:#666;white-space:nowrap}
.bar{position:absolute;bottom:45px;width:18px}
/* ring */
.ring-head{font-size:6.6px;color:#666;font-weight:600}
.ring-sub{font-size:5px;line-height:7.6px;color:#888}
/* closing */
.closing{background:var(--red)}
.closing::after{display:none}
.thanks{position:absolute;left:203px;top:84px;font-family:"Roboto Condensed",Arial,sans-serif;font-size:17px;color:var(--white);white-space:nowrap}
.contact-box{position:absolute;left:203px;top:113px;right:0;height:102px;background:var(--white);padding:10px 12px}
.contact-box .intro{font-size:8.4px;line-height:11.5px;color:#555}
.contact-list{list-style:none;margin-top:12px}
.contact-list li{display:flex;align-items:center;gap:6px;font-size:8.4px;color:#555;line-height:12px;white-space:nowrap}
.contact-list svg{width:8px;height:8px}
.closing-brand{position:absolute;left:34px;top:158px;white-space:nowrap}
.closing-brand .brand-dot{width:20px;height:20px}
.closing-brand .brand-name{font-size:28px}
.closing-brand .brand-sub{display:block;margin:3px 0 0 24px;font-size:9px;letter-spacing:2px;color:var(--white);line-height:1}
</style>
</head>
<body>

<!-- Cover, light -->
<section class="slide col-1 row-1">
  <div class="cover-block">
    <div class="cover-title"><span class="accent">Project</span> Title Here</div>
    <p class="cover-sub">Subtext here Subtext here Subtext here<br>Subtext here Subtext here Subtext here</p>
  </div>
  <div class="cover-brand">
    <div class="brand"><span class="brand-dot"></span><span class="brand-name">Tavrel</span></div>
    <span class="brand-sub">PHYTOCOR</span>
  </div>
  <div class="cover-stripe"></div>
</section>

<!-- Cover, red -->
<section class="slide col-2 row-1">
  <div class="cover-red"></div>
  <div class="cover-block">
    <div class="cover-title" style="color:var(--white)">Project Title Here</div>
    <p class="cover-sub" style="color:#f6d6d7">Subtext here Subtext here Subtext here<br>Subtext here Subtext here Subtext here</p>
  </div>
  <div class="cover-brand">
    <div class="brand"><span class="brand-dot"></span><span class="brand-name">Tavrel</span></div>
    <span class="brand-sub">PHYTOCOR</span>
  </div>
</section>

<!-- Table -->
<section class="slide col-3 row-1">
  <header class="header"><span class="header-title">Project Title Here</span><span class="brand"><span class="brand-dot"></span><span class="brand-name">Tavrel</span></span></header>
  <div class="abs red-head" style="left:28px;top:60px">Table Head Here</div>
  <p class="abs lorem" style="left:32px;top:72px;width:320px;height:28px">Lorem ipsum dolor sit Lorem ipsum dolor sit Lorem ipsum dolor sit Lorem ipsum dolor sit Lorem ipsum dolor sit Lorem ipsum dolor sit Lorem ipsum dolor sit Lorem ipsum dolor sit Lorem ipsum dolor sit Lorem ipsum dolor sit Lorem ipsum dolor sit Lorem ipsum dolor sit Lorem ipsum dolor sit Lorem ipsum dolor sit Lorem ipsum dolor sit Lorem ipsum dolor sit</p>
  <table class="data-table">
    <tr><th>TABLE HEAD HERE</th><th>TABLE HEAD HERE</th><th>TABLE HEAD HERE</th></tr>
    <tr><td>Subtext here Subtext here</td><td>Subtext here Subtext here</td><td>Subtext here Subtext here</td></tr>
    <tr><td>Subtext here Subtext here</td><td>Subtext here Subtext here</td><td>Subtext here Subtext here</td></tr>
    <tr><td>Subtext here Subtext here</td><td>Subtext here Subtext here</td><td>Subtext here Subtext here</td></tr>
    <tr><td>Subtext here Subtext here</td><td>Subtext here Subtext here</td><td>Subtext here Subtext here</td></tr>
    <tr><td>Subtext here Subtext here</td><td>Subtext here Subtext here</td><td>Subtext here Subtext here</td></tr>
    <tr><td>Subtext here Subtext here</td><td>Subtext here Subtext here</td><td>Subtext here Subtext here</td></tr>
  </table>
</section>

<!-- Two column paragraphs -->
<section class="slide col-1 row-2">
  <header class="header"><span class="header-title">Project Title Here</span><span class="brand"><span class="brand-dot"></span><span class="brand-name">Tavrel</span></span></header>
  <div class="abs" style="left:29px;top:50px;width:150px">
    <div class="para-head">Paragraph text</div>
    <p class="lorem" style="margin-top:4px;height:74px">Lorem ipsum dolor sit Lorem ipsum dolor sit Lorem ipsum dolor sit Lorem ipsum dolor sit Lorem ipsum dolor sit Lorem ipsum dolor sit Lorem ipsum dolor sit Lorem ipsum dolor sit Lorem ipsum dolor sit Lorem ipsum dolor sit Lorem ipsum dolor sit Lorem ipsum dolor sit Lorem ipsum dolor sit Lorem ipsum dolor sit Lorem ipsum dolor sit Lorem ipsum dolor sit Lorem ipsum</p>
    <p class="lorem" style="margin-top:9px;height:74px">Lorem ipsum dolor sit Lorem ipsum dolor sit Lorem ipsum dolor sit Lorem ipsum dolor sit Lorem ipsum dolor sit Lorem ipsum dolor sit Lorem ipsum dolor sit Lorem ipsum dolor sit Lorem ipsum dolor sit Lorem ipsum dolor sit Lorem ipsum dolor sit Lorem ipsum dolor sit Lorem ipsum dolor sit Lorem ipsum dolor sit Lorem ipsum dolor sit Lorem ipsum dolor sit Lorem ipsum</p>
    <p class="lorem" style="margin-top:9px;height:37px">Lorem ipsum dolor sit Lorem ipsum dolor sit Lorem ipsum dolor sit Lorem ipsum dolor sit Lorem ipsum dolor sit Lorem ipsum dolor sit Lorem ipsum dolor sit Lorem ipsum dolor sit Lorem ipsum</p>
  </div>
  <div class="abs" style="left:210px;top:50px;width:150px">
    <div class="para-head">Paragraph text</div>
    <p class="lorem" style="margin-top:4px;height:74px">Lorem ipsum dolor sit Lorem ipsum dolor sit Lorem ipsum dolor sit Lorem ipsum dolor sit Lorem ipsum dolor sit Lorem ipsum dolor sit Lorem ipsum dolor sit Lorem ipsum dolor sit Lorem ipsum dolor sit Lorem ipsum dolor sit Lorem ipsum dolor sit Lorem ipsum dolor sit Lorem ipsum dolor sit Lorem ipsum dolor sit Lorem ipsum dolor sit Lorem ipsum dolor sit Lorem ipsum</p>
    <p class="lorem" style="margin-top:9px;height:74px">Lorem ipsum dolor sit Lorem ipsum dolor sit Lorem ipsum dolor sit Lorem ipsum dolor sit Lorem ipsum dolor sit Lorem ipsum dolor sit Lorem ipsum dolor sit Lorem ipsum dolor sit Lorem ipsum dolor sit Lorem ipsum dolor sit Lorem ipsum dolor sit Lorem ipsum dolor sit Lorem ipsum dolor sit Lorem ipsum dolor sit Lorem ipsum dolor sit Lorem ipsum dolor sit Lorem ipsum</p>
    <p class="lorem" style="margin-top:9px;height:37px">Lorem ipsum dolor sit Lorem ipsum dolor sit Lorem ipsum dolor sit Lorem ipsum dolor sit Lorem ipsum dolor sit Lorem ipsum dolor sit Lorem ipsum dolor sit Lorem ipsum dolor sit Lorem ipsum</p>
  </div>
</section>

<!-- Bullets -->
<section class="slide col-2 row-2">
  <header class="header"><span class="header-title">Project Title Here</span><span class="brand"><span class="brand-dot"></span><span class="brand-name">Tavrel</span></span></header>
  <div class="abs" style="left:18px;top:52px;width:348px">
    <div class="bullet-head">Bullet Title Heading Here Bullet Title Heading Here</div>
    <p class="lorem" style="margin:3px 0 0 12px;height:28px">Lorem ipsum dolor sit Lorem ipsum dolor sit Lorem ipsum dolor sit Lorem ipsum dolor sit Lorem ipsum dolor sit Lorem ipsum dolor sit Lorem ipsum dolor sit Lorem ipsum dolor sit Lorem ipsum dolor sit Lorem ipsum dolor sit Lorem ipsum dolor sit Lorem ipsum dolor sit Lorem ipsum dolor sit Lorem ipsum dolor sit Lorem ipsum dolor sit Lorem ipsum dolor sit</p>
    <div class="bullet-head" style="margin-top:14px">Bullet Title Heading Here Bullet Title Heading Here</div>
    <p class="lorem" style="margin:3px 0 0 12px;height:28px">Lorem ipsum dolor sit Lorem ipsum dolor sit Lorem ipsum dolor sit Lorem ipsum dolor sit Lorem ipsum dolor sit Lorem ipsum dolor sit Lorem ipsum dolor sit Lorem ipsum dolor sit Lorem ipsum dolor sit Lorem ipsum dolor sit Lorem ipsum dolor sit Lorem ipsum dolor sit Lorem ipsum dolor sit Lorem ipsum dolor sit Lorem ipsum dolor sit Lorem ipsum dolor sit</p>
    <div class="bullet-head" style="margin-top:17px">Bullet Title Heading Here Bullet Title Heading Here</div>
    <p class="lorem" style="margin:3px 0 0 12px;height:28px">Lorem ipsum dolor sit Lorem ipsum dolor sit Lorem ipsum dolor sit Lorem ipsum dolor sit Lorem ipsum dolor sit Lorem ipsum dolor sit Lorem ipsum dolor sit Lorem ipsum dolor sit Lorem ipsum dolor sit Lorem ipsum dolor sit Lorem ipsum dolor sit Lorem ipsum dolor sit Lorem ipsum dolor sit Lorem ipsum dolor sit Lorem ipsum dolor sit Lorem ipsum dolor sit</p>
    <div class="bullet-head" style="margin-top:14px">Bullet Title Heading Here Bullet Title Heading Here</div>
    <p class="lorem" style="margin:3px 0 0 12px;height:28px">Lorem ipsum dolor sit Lorem ipsum dolor sit Lorem ipsum dolor sit Lorem ipsum dolor sit Lorem ipsum dolor sit Lorem ipsum dolor sit Lorem ipsum dolor sit Lorem ipsum dolor sit Lorem ipsum dolor sit Lorem ipsum dolor sit Lorem ipsum dolor sit Lorem ipsum dolor sit Lorem ipsum dolor sit Lorem ipsum dolor sit Lorem ipsum dolor sit Lorem ipsum dolor sit</p>
  </div>
</section>

<!-- Timeline -->
<section class="slide col-3 row-2">
  <header class="header"><span class="header-title">Project Title Here</span><span class="brand"><span class="brand-dot"></span><span class="brand-name">Tavrel</span></span></header>
  <div class="abs red-head" style="left:14px;top:46px">Lorem ipsum dolor sit Lorem ipsum dolor sit &nbsp;Lorem ipsum dolor sit</div>
  <p class="abs lorem" style="left:14px;top:59px;width:350px;height:28px">Lorem ipsum dolor sit Lorem ipsum dolor sit Lorem ipsum dolor sit Lorem ipsum dolor sit Lorem ipsum dolor sit Lorem ipsum dolor sit Lorem ipsum dolor sit Lorem ipsum dolor sit Lorem ipsum dolor sit Lorem ipsum dolor sit Lorem ipsum dolor sit Lorem ipsum dolor sit Lorem ipsum dolor sit Lorem ipsum dolor sit Lorem ipsum dolor sit</p>
  <div class="t-line"></div>
  <div class="year" style="left:50px;top:100px">1995</div>
  <div class="year" style="left:168px;top:100px">2005</div>
  <div class="year grey" style="left:292px;top:100px">2015</div>
  <div class="t-card" style="left:15px"><div class="t-card-head">TITLE HERE</div><p>Lorem ipsum dolor sit Lorem ipsum dolor sit Lorem ipsum dolor sit Lorem ipsum dolor sit Lorem ipsum dolor sit Lorem ipsum dolor sit Lorem ipsum dolor sit Lorem ipsum dolor sit Lorem ipsum dolor sit Lorem ipsum dolor sit</p></div>
  <div class="t-card" style="left:134px"><div class="t-card-head">TITLE HERE</div><p>Lorem ipsum dolor sit Lorem ipsum dolor sit Lorem ipsum dolor sit Lorem ipsum dolor sit Lorem ipsum dolor sit Lorem ipsum dolor sit Lorem ipsum dolor sit Lorem ipsum dolor sit Lorem ipsum dolor sit Lorem ipsum dolor sit</p></div>
  <div class="t-card grey" style="left:257px"><div class="t-card-head">TITLE HERE</div><p>Lorem ipsum dolor sit Lorem ipsum dolor sit Lorem ipsum dolor sit Lorem ipsum dolor sit Lorem ipsum dolor sit Lorem ipsum dolor sit Lorem ipsum dolor sit Lorem ipsum dolor sit Lorem ipsum dolor sit Lorem ipsum dolor sit</p></div>
</section>

<!-- Bar chart -->
<section class="slide col-1 row-3">
  <header class="header"><span class="header-title">Project Title Here</span><span class="brand"><span class="brand-dot"></span><span class="brand-name">Tavrel</span></span></header>
  <div class="abs bullet-head" style="left:20px;top:51px">Bullet Title Heading Here Bullet Title Heading Here</div>
  <p class="abs lorem" style="left:32px;top:62px;width:335px;height:28px">Lorem ipsum dolor sit Lorem ipsum dolor sit Lorem ipsum dolor sit Lorem ipsum dolor sit Lorem ipsum dolor sit Lorem ipsum dolor sit Lorem ipsum dolor sit Lorem ipsum dolor sit Lorem ipsum dolor sit Lorem ipsum dolor sit Lorem ipsum dolor sit Lorem ipsum dolor sit Lorem ipsum dolor sit Lorem ipsum dolor sit Lorem ipsum dolor sit</p>
  <span class="axis-label" style="top:105px">Lorem ipsum dolor sit</span>
  <span class="axis-label" style="top:121px">Lorem ipsum dolor sit</span>
  <span class="axis-label" style="top:138px">Lorem ipsum dolor sit</span>
  <span class="axis-label" style="top:155px">Lorem ipsum dolor sit</span>
  <span class="axis-label" style="top:172px">Lorem ipsum dolor sit</span>
  <span class="axis-label" style="top:190px">Lorem ipsum dolor sit</span>
  <span class="axis-label" style="top:233px">Lorem ipsum dolor sit</span>
  <div class="abs" style="left:89px;top:104px;width:1px;height:134px;background:#ccc"></div>
  <div class="bar" style="left:94px;height:44px;background:var(--red-mid)"></div>
  <div class="bar" style="left:117px;height:78px;background:var(--red)"></div>
  <div class="bar" style="left:140px;height:65px;background:var(--red-dark)"></div>
  <div class="bar" style="left:164px;height:39px;background:#9a9a9a"></div>
  <div class="bar" style="left:187px;height:11px;background:var(--red)"></div>
  <div class="bar" style="left:211px;height:4px;background:#8a8a8a"></div>
  <div class="bar" style="left:235px;height:123px;background:var(--red-dark)"></div>
  <div class="bar" style="left:259px;height:12px;background:var(--red)"></div>
  <div class="bar" style="left:283px;height:6px;background:#a5a5a5"></div>
  <div class="bar" style="left:307px;height:3px;background:#999"></div>
</section>

<!-- Ring diagram -->
<section class="slide col-2 row-3">
  <header class="header"><span class="header-title">Project Title Here</span><span class="brand"><span class="brand-dot"></span><span class="brand-name">Tavrel</span></span></header>
  <svg class="abs" style="left:0;top:0" width="380" height="283" viewBox="0 0 380 283" aria-hidden="true">
    <g fill="none" stroke-width="13" transform="translate(188 139)">
      <circle r="64" stroke="#8c1a24" stroke-dasharray="42 360" transform="rotate(-112)"/>
      <circle r="64" stroke="var(--red-dark)" stroke-dasharray="42 360" transform="rotate(-67)"/>
      <circle r="64" stroke="var(--red)" stroke-dasharray="42 360" transform="rotate(-22)"/>
      <circle r="64" stroke="var(--steel)" stroke-dasharray="42 360" transform="rotate(23)"/>
      <circle r="64" stroke="var(--slate)" stroke-dasharray="42 360" transform="rotate(68)"/>
      <circle r="64" stroke="var(--navy)" stroke-dasharray="42 360" transform="rotate(113)"/>
      <circle r="64" stroke="#6b6b6b" stroke-dasharray="42 360" transform="rotate(158)"/>
      <circle r="64" stroke="#d9676e" stroke-dasharray="42 360" transform="rotate(203)"/>
      <circle r="16" fill="var(--red)" stroke="none"/>
    </g>
    <g stroke="#555" stroke-width="0.8" fill="none">
      <polyline points="150,83 130,68 100,68"/>
      <polyline points="232,85 260,65 300,65"/>
      <polyline points="255,140 265,133 300,133"/>
      <polyline points="225,195 250,208 300,208"/>
      <polyline points="122,150 110,147 98,147"/>
      <polyline points="140,196 120,216 98,216"/>
    </g>
  </svg>
  <div class="abs" style="left:40px;top:73px;width:75px"><div class="ring-head">Heading Here</div><p class="ring-sub">Subtext here Subtext here Subtext here Subtext here Subtext here</p></div>
  <div class="abs" style="left:40px;top:148px;width:75px"><div class="ring-head">Heading Here</div><p class="ring-sub">Subtext here Subtext here Subtext here Subtext here Subtext here</p></div>
  <div class="abs" style="left:40px;top:215px;width:55px"><div class="ring-head">Heading Here</div><p class="ring-sub">Subtext here Subtext here Subtext here Subtext here</p></div>
  <div class="abs" style="left:270px;top:64px;width:80px;text-align:right"><div class="ring-head">Heading Here</div><p class="ring-sub">Subtext here Subtext here Subtext here Subtext here Subtext here</p></div>
  <div class="abs" style="left:270px;top:131px;width:80px;text-align:right"><div class="ring-head">Heading Here</div><p class="ring-sub">Subtext here Subtext here Subtext here Subtext here Subtext here</p></div>
  <div class="abs" style="left:270px;top:206px;width:80px;text-align:right"><div class="ring-head">Heading Here</div><p class="ring-sub">Subtext here Subtext here Subtext here Subtext here Subtext here</p></div>
</section>

<!-- Closing -->
<section class="slide col-3 row-3 closing">
  <div class="closing-brand">
    <div class="brand"><span class="brand-dot"></span><span class="brand-name">Tavrel</span></div>
    <span class="brand-sub">PHYTOCOR</span>
  </div>
  <div class="thanks">Thanks for your Time</div>
  <div class="contact-box">
    <p class="intro">Lorem ipsum dolor sit amet,<br>consectetur adipiscing elit.<br>Donec accumsan.</p>
    <ul class="contact-list">
      <li><svg viewBox="0 0 10 10"><path d="M2 1l2 2-1 1.5c.6 1.2 1.3 1.9 2.5 2.5L7 6l2 2-1.5 1.5C4.5 9 1 5.5.5 2.5z" fill="#555"/></svg>: 604 555 0199</li>
      <li><svg viewBox="0 0 10 10"><rect x="0.5" y="2" width="9" height="6" fill="#555"/><path d="M.5 2l4.5 3.5L9.5 2" stroke="#fff" stroke-width=".8" fill="none"/></svg>: info@tavrelphytocor.ca</li>
      <li><svg viewBox="0 0 10 10"><path d="M9 1L1 5l3 1 1 3z" fill="#555"/></svg>: tavrelphytocor.ca</li>
    </ul>
  </div>
</section>

</body>
</html>
```